Home page design for Drone video business (the Business focusses on home videos for realtors)

Dear reader,

*I NEED DESIGNS OF ALL THE PAGES*
We need a first design of a homepage and of 4 other pages of the website of a business that sells drone video services. All the pages will need to be in the similar design style.
The video's are targeted at consumers that want to sell there home and would like to have a cool drone video of photos of their home.

How does the website look:
- has a navbar on top
- A cool looking banner of an areal drone.
- A Big header: with company name: SkyLoftReels
- A smaller subheader: We film your home to increase your chances of sale
- Then a section with a Big header: How does it work
- In this section a place for a vimeo explainitory video
- Then a similar navbar styled bar with a phone number and a email address
- Then a section where the videos porfolio is displayed in a cool way
- Inside this sectiona header: Our work

- A section with header: Why us?
- 4 symbols here with a subheader and some lorum ipsum text underneath (see wireframe images)

- Under that a: Contact us
- where you can put in name, email, phone, message box and a send button

- At the bottom a footer with phone number and a fake address for now.

Be creative. Use creative but serious color.
Use a serious font. Make it a sharp design. Sharp lines. Not to dark design and not to light design.

The wireframes are the same kind of images.
PLEASE PUT IN DESIGNS OF ALL THE PAGES

Good luck

Target Market(s)

People that want to sell home and want to make a cool drone video or photos of their home.

Industry/Entity Type

Business

Contact Information for Business Card

Lucas Wenning
lucas@skyloftreels.example
+31647208351

Logo Text

SkyLoftReels

Number of Pages Required

1 page

Font styles to use
Sans Serif

Requirements
Must have
• All the sections as explained in the instructions.
• The nav bar should have an about us, services, portfolio and a contact us buttons.
• See instruction for details.
• Must include designs of the front page, contact us, our services, portfolio and contact us.
• If you do add some designs for the "about us", "services", "prices", "portfolio" and "contact us" pages, you make a way better chance of winning the competition.
Nice to have
• designs for the other pages as described at the Must haves. You make a better chance of winning if you include them. Look at the wireframes to see the mockups for those pages. think creative about what kind of sections and design should be included in those pages.
Should not have
• bad designs.

```html
<!DOCTYPE html>
<html lang="en">
<head>
<meta charset="utf-8">
<title>SkyLoftReels – Contact Us</title>
<link href="https://fonts.googleapis.com/css2?family=Lato:wght@400;700&display=swap" rel="stylesheet">
<style>
  :root {
    --teal: #0b6870;
    --teal-dark: #09606a;
    --teal-line: #4a9ea4;
    --ink: #1d1d1d;
    --muted: #8a8a8a;
    --field: #c9c9c9;
    --crumb: #eeeeee;
    --footer: #0a666e;
    --footer-line: #2f8089;
    --bottom: #0e0e0e;
    --white: #ffffff;
  }
  * { box-sizing: border-box; margin: 0; padding: 0; }
  html, body { width: 1011px; height: 1200px; overflow: hidden; background: var(--white); }
  body { position: relative; font-family: 'Lato', sans-serif; color: var(--ink); }

  /* header */
  .site-header { position: absolute; left: 0; top: 0; width: 1011px; height: 100px; border-bottom: 1px solid #d9d9d9; }
  .brand { position: absolute; left: 83px; top: 64px; display: flex; align-items: center; gap: 8px; font-family: 'Lato', sans-serif; font-size: 22px; font-weight: 700; color: var(--ink); }
  .brand-mark { width: 14px; height: 14px; background: var(--teal); }
  .top-contact { position: absolute; top: 12px; display: flex; align-items: center; gap: 9px; font-size: 16px; color: #333; }
  .top-contact .dot { width: 30px; height: 30px; border-radius: 50%; background: var(--teal); display: flex; align-items: center; justify-content: center; }
  .main-nav { position: absolute; top: 70px; left: 418px; display: flex; gap: 36px; font-size: 12.5px; font-weight: 700; color: #222; }
  .main-nav a { text-decoration: none; color: inherit; position: relative; padding-bottom: 20px; }
  .main-nav a.current { color: var(--teal); }
  .main-nav a.active::after { content: ""; position: absolute; left: 0; right: 0; bottom: -1px; height: 3px; background: var(--teal); }

  /* hero */
  .hero { position: absolute; left: 0; top: 100px; width: 1011px; height: 282px;
    background:
      radial-gradient(ellipse 260px 150px at 880px 110px, rgba(92,140,58,.9), transparent 70%),
      radial-gradient(ellipse 220px 160px at 60px 140px, rgba(58,92,48,.9), transparent 70%),
      radial-gradient(ellipse 300px 130px at 500px 90px, rgba(112,116,120,.85), transparent 70%),
      radial-gradient(ellipse 380px 140px at 520px 230px, rgba(146,84,62,.85), transparent 70%),
      linear-gradient(180deg, #a9c3dc 0%, #6f8f5a 22%, #6c6a5e 50%, #7a5a4a 78%, #56664f 100%); }
  .hero-band { position: absolute; left: 0; top: 209px; width: 1011px; height: 73px; background: rgba(11,104,112,.88); text-align: center; color: var(--white); }
  .hero-band h1 { font-family: 'Lato', sans-serif; font-size: 33px; font-weight: 400; margin-top: 6px; letter-spacing: .3px; line-height: 1.1; }
  .hero-band p { font-family: 'Lato', sans-serif; font-size: 18.5px; margin-top: 2px; }

  .crumbs { position: absolute; left: 0; top: 382px; width: 1011px; height: 32px; background: var(--crumb); display: flex; align-items: center; padding-left: 105px; gap: 8px; font-size: 10.5px; font-weight: 700; color: var(--teal); }
  .crumbs .sep { color: #777; font-weight: 400; }

  .page-title { position: absolute; top: 446px; left: 0; width: 1011px; text-align: center; font-size: 27px; font-weight: 700; color: var(--teal); }

  .info-card { position: absolute; top: 494px; height: 92px; background: var(--teal-dark); padding: 5px; }
  .info-card .inner { height: 100%; border: 1px solid var(--teal-line); display: flex; align-items: center; padding-left: 18px; gap: 18px; color: var(--white); }
  .info-card .ring { width: 48px; height: 48px; border-radius: 50%; border: 2px solid var(--white); display: flex; align-items: center; justify-content: center; flex: none; }
  .info-card h3 { font-size: 14px; font-weight: 700; margin-bottom: 4px; }
  .info-card p { font-size: 13.5px; line-height: 1.2; }
  .info-card p.small { font-size: 11px; line-height: 1.38; }

  /* form */
  .form-title { position: absolute; left: 84px; top: 641px; width: 379px; font-size: 19.5px; font-weight: 700; color: var(--teal); padding-bottom: 11px; border-bottom: 2px solid #d0d0d0; }
  .field { position: absolute; border: 1px solid var(--field); font-size: 11px; color: var(--muted); padding: 11px 7px; }
  .submit { position: absolute; left: 84px; top: 872px; width: 104px; height: 32px; background: var(--teal); color: var(--white); font-size: 15px; display: flex; align-items: center; justify-content: center; box-shadow: 0 6px 6px -4px rgba(0,0,0,.35); }
  .map-box { position: absolute; left: 497px; top: 645px; width: 431px; height: 260px; border: 1px solid #9a9a9a; padding: 4px; }
  .map-fill { width: 100%; height: 100%;
    background:
      radial-gradient(ellipse 120px 80px at 230px 140px, rgba(255,255,255,.6), transparent 70%),
      linear-gradient(135deg, #ece8e0 0%, #e4dfd6 55%, #dcd6cb 100%); }

  /* footer */
  .site-footer { position: absolute; left: 0; top: 941px; width: 1011px; height: 222px; background: var(--footer); color: var(--white); }
  .f-col { position: absolute; top: 32px; }
  .f-col h4 { font-size: 14.5px; font-weight: 700; padding-bottom: 6px; border-bottom: 1px solid var(--footer-line); white-space: nowrap; }
  .f-sep { position: absolute; top: 45px; width: 1px; height: 140px; background: var(--footer-line); }
  .links { list-style: none; font-size: 12px; margin-top: 4px; }
  .links li { height: 23.2px; display: flex; align-items: center; gap: 6px; }
  .detail { font-size: 11.5px; font-weight: 700; margin-top: 11px; }
  .detail li { list-style: none; display: flex; gap: 9px; align-items: flex-start; margin-bottom: 19px; }
  .detail .note { font-weight: 400; line-height: 1.25; }
  .f-map { position: absolute; left: 472px; top: 65px; width: 226px; height: 128px;
    background:
      radial-gradient(ellipse 90px 50px at 150px 50px, rgba(255,255,255,.55), transparent 70%),
      linear-gradient(135deg, #ece8e0, #ddd8cf); }
  .f-brand { position: absolute; left: 750px; top: 98px; font-size: 21px; font-weight: 700; color: #d6dde0; display: flex; align-items: center; gap: 8px; }
  .f-brand .sq { width: 12px; height: 12px; background: #d6dde0; }

  .bottom-bar { position: absolute; left: 0; top: 1163px; width: 1011px; height: 37px; background: var(--bottom); color: #e6e6e6; font-size: 10.5px; }
  .bottom-bar .copy { position: absolute; left: 83px; top: 12px; }
  .social { position: absolute; top: 10px; width: 18px; height: 18px; border-radius: 50%; border: 1px solid #cfcfcf; }
</style>
</head>
<body>

<header class="site-header">
  <div class="brand"><span class="brand-mark"></span>SkyLoftReels</div>
  <div class="top-contact" style="left:601px">
    <span class="dot"><svg width="14" height="14" viewBox="0 0 24 24"><path fill="#fff" d="M6.6 10.8a15 15 0 0 0 6.6 6.6l2.2-2.2a1 1 0 0 1 1-.25 11.4 11.4 0 0 0 3.6.57 1 1 0 0 1 1 1V20a1 1 0 0 1-1 1A17 17 0 0 1 3 4a1 1 0 0 1 1-1h3.5a1 1 0 0 1 1 1c0 1.25.2 2.45.57 3.57a1 1 0 0 1-.25 1z"/></svg></span>
    +31 647 208 351
  </div>
  <div class="top-contact" style="left:774px;font-size:13px">
    <span class="dot"><svg width="15" height="11" viewBox="0 0 20 14"><rect x="1" y="1" width="18" height="12" fill="none" stroke="#fff" stroke-width="1.6"/><path d="M1 1l9 7 9-7" fill="none" stroke="#fff" stroke-width="1.6"/></svg></span>
    lucas@skyloftreels.example
  </div>
  <nav class="main-nav">
    <a class="current" href="#">HOME</a>
    <a href="#">ABOUT US</a>
    <a href="#">SERVICES</a>
    <a href="#">PORTFOLIO</a>
    <a href="#">PRICES</a>
    <a class="active" href="#">CONTACT US</a>
  </nav>
</header>

<section class="hero" role="img" aria-label="Aerial photo of a brick family home among trees with a drone hovering over the roof">
  <div class="hero-band">
    <h1>SKYLOFTREELS</h1>
    <p>We Film Your Home To Increase Your Chances Of Sale</p>
  </div>
</section>

<div class="crumbs">
  <svg width="14" height="12" viewBox="0 0 24 20"><path fill="#333" d="M12 1 1 10h3v9h6v-6h4v6h6v-9h3z"/></svg>
  <span class="sep">/</span><span>CONTACT US</span>
</div>

<h2 class="page-title">CONTACT US</h2>

<div class="info-card" style="left:83px;width:307px">
  <div class="inner">
    <span class="ring"><svg width="20" height="24" viewBox="0 0 20 24"><rect x="3" y="2" width="14" height="20" fill="none" stroke="#fff" stroke-width="1.6"/><g fill="#fff"><rect x="6" y="5" width="2" height="2"/><rect x="9" y="5" width="2" height="2"/><rect x="12" y="5" width="2" height="2"/><rect x="6" y="9" width="2" height="2"/><rect x="9" y="9" width="2" height="2"/><rect x="12" y="9" width="2" height="2"/><rect x="6" y="13" width="2" height="2"/><rect x="9" y="13" width="2" height="2"/><rect x="12" y="13" width="2" height="2"/><rect x="8" y="17" width="4" height="5"/></g></svg></span>
    <div>
      <h3>LOCATION</h3>
      <p class="small">Lorem ipsum dolor sit amet, consectetuer adipiscing elit, sed diam nonummy nibh d tincidunt ut laoreet dolore magna.</p>
    </div>
  </div>
</div>

<div class="info-card" style="left:416px;width:235px">
  <div class="inner">
    <span class="ring"><svg width="20" height="20" viewBox="0 0 24 24"><path fill="#fff" d="M6.6 10.8a15 15 0 0 0 6.6 6.6l2.2-2.2a1 1 0 0 1 1-.25 11.4 11.4 0 0 0 3.6.57 1 1 0 0 1 1 1V20a1 1 0 0 1-1 1A17 17 0 0 1 3 4a1 1 0 0 1 1-1h3.5a1 1 0 0 1 1 1c0 1.25.2 2.45.57 3.57a1 1 0 0 1-.25 1z"/></svg></span>
    <div>
      <h3>CALL US ON</h3>
      <p>+31 647 208 351</p>
    </div>
  </div>
</div>

<div class="info-card" style="left:679px;width:249px">
  <div class="inner">
    <span class="ring"><svg width="22" height="16" viewBox="0 0 20 14"><rect x="1" y="1" width="18" height="12" rx="1.5" fill="none" stroke="#fff" stroke-width="1.5"/><path d="M1 2l9 6 9-6" fill="none" stroke="#fff" stroke-width="1.5"/></svg></span>
    <div>
      <h3>Email</h3>
      <p style="font-size:12px">lucas@skyloftreels.example</p>
    </div>
  </div>
</div>

<h2 class="form-title">LEAVE&nbsp; A MESSAGE</h2>
<div class="field" style="left:84px;top:699px;width:379px;height:32px">Name</div>
<div class="field" style="left:84px;top:745px;width:184px;height:32px">Email Id</div>
<div class="field" style="left:279px;top:745px;width:184px;height:32px">Phone</div>
<div class="field" style="left:84px;top:790px;width:379px;height:60px;padding-top:8px">Message</div>
<div class="submit">Submit</div>

<div class="map-box"><div class="map-fill" role="img" aria-label="Street map of the neighbourhood around the office"></div></div>

<footer class="site-footer">
  <div class="f-col" style="left:83px;width:87px">
    <h4>Quick Links</h4>
    <ul class="links">
      <li>› Home</li><li>› About Us</li><li>› Services</li><li>› Portfolio</li><li>› Prices</li><li>› Contact Us</li>
    </ul>
  </div>
  <div class="f-sep" style="left:196px"></div>

  <div class="f-col" style="left:231px;width:200px">
    <h4 style="display:inline-block;padding-right:12px">Contact Detail</h4>
    <ul class="detail">
      <li><svg width="10" height="15" viewBox="0 0 10 15"><path fill="#fff" d="M5 0a5 5 0 0 1 5 5c0 3.5-5 10-5 10S0 8.5 0 5a5 5 0 0 1 5-5zm0 3a2 2 0 1 0 0 4 2 2 0 0 0 0-4z"/></svg><span class="note"><b>SkyLoftReels,</b> Lorem ipsum dolor sit amet, consectetuer auyipiscing elit</span></li>
      <li><svg width="13" height="13" viewBox="0 0 24 24"><path fill="#fff" d="M6.6 10.8a15 15 0 0 0 6.6 6.6l2.2-2.2a1 1 0 0 1 1-.25 11.4 11.4 0 0 0 3.6.57 1 1 0 0 1 1 1V20a1 1 0 0 1-1 1A17 17 0 0 1 3 4a1 1 0 0 1 1-1h3.5a1 1 0 0 1 1 1c0 1.25.2 2.45.57 3.57a1 1 0 0 1-.25 1z"/></svg>+31 647 208 351</li>
      <li><svg width="13" height="13" viewBox="0 0 16 16"><rect x="4" y="1" width="8" height="4" fill="#fff"/><rect x="1" y="5" width="14" height="7" fill="#fff"/><rect x="4" y="10" width="8" height="5" fill="#fff" stroke="#0a666e" stroke-width="1"/></svg>+31 647 208 351</li>
      <li><svg width="14" height="10" viewBox="0 0 20 14"><rect x="0" y="0" width="20" height="14" fill="#fff"/><path d="M0 0l10 8 10-8" fill="none" stroke="#0a666e" stroke-width="1.5"/></svg>lucas@skyloftreels.example</li>
    </ul>
  </div>
  <div class="f-sep" style="left:445px"></div>

  <div class="f-col" style="left:472px;width:110px">
    <h4>Map</h4>
  </div>
  <div class="f-map" role="img" aria-label="Small street map with a pin on the office address"></div>
  <div class="f-sep" style="left:724px"></div>

  <div class="f-brand"><span class="sq"></span>SkyLoftReels</div>
</footer>

<div class="bottom-bar">
  <span class="copy">Copyright © 2016 SkyLoftReels.&nbsp; All Rights Reserved</span>
  <span class="social" style="left:860px" aria-label="Social link"></span>
  <span class="social" style="left:885px" aria-label="Social link"></span>
  <span class="social" style="left:910px" aria-label="Social link"></span>
</div>

</body>
</html>
```